Ridge Lass Crew (Flyer)

I want a flyer to advertise my service.
Details below, and logo's to use are attached.

A girls only after school program, 11-14yrs, as OSHC is no longer avail, dedicated to coaching & mentoring our girls into strong, independent young women.

The Brainchild of Rebecca Folwin, Ridge Lass Crew was created to address the growing demand for after school/school holiday supervision for kids moving from primary into high school, when OSHC ceases to exist.
With over 12 years experience mentoring and coaching young women in the corporate world, Bec decided to leave her role as a Director with Tarrant Trust, and follow her passion.
Bec, along with her sister Lorraine, who has over 10 years experience in local communities as a Youth Worker, and is also a qualified Enrolled Nurse, embarked on building a program designed to keep parents happy (by knowing their girls are safe) and dedicated to coaching and mentoring our girls into strong, independent young women.
Open every afternoon and during school holidays, we look to offer;
- Daily meditation
- Healthy snacks
- Dedicated homework time
- Organised group activity, led by qualified instructors (yoga, fitness class, soccer etc)
- Regular guests speakers, addressing issues/concerns for young people today
- SOCIAL MEDIA FREE ZONE

Located 87 Pelham Pde, Baulkham Hills (across from Crestmoor Day Clinic)
Open 3-6pm Monday to Friday

Facebook page: http://fb.example/ridgelasscrew
Email: info@ridgelasscrew.example.au
Mobile: 0455817396

Target Market(s)

Parents of teenage girls, teenage girls 11-14 years

Industry/Entity Type

School

Font styles to use
Sans Serif

Colors
b768aa
e667a6

Requirements
Must have
• What progam is - see brief
• Who runs it
Should not have
• Not be too busy, not overly mature images

```html
<!DOCTYPE html>
<html lang="en">
<head>
<meta charset="utf-8">
<title>Ridge Lass Crew – After School Program Flyer</title>
<link href="https://fonts.googleapis.com/css2?family=Cinzel:wght@500;600&family=Open+Sans:wght@600;700&family=Roboto+Condensed:wght@700&family=Share+Tech+Mono&family=Archivo:wght@700&display=swap" rel="stylesheet">
<style>
  :root {
    --purple: #b768aa;
    --purple-deep: #a65f9e;
    --pink: #e667a6;
    --pink-soft: #e58ab5;
    --blush: #f2c3cf;
    --white: #ffffff;
    --ink: #1c1520;
    --frame: #fbf8f6;
  }
  html, body {
    margin: 0;
    padding: 0;
    width: 848px;
    height: 1200px;
    overflow: hidden;
    background: var(--white);
  }
  .flyer {
    position: relative;
    width: 848px;
    height: 1200px;
    overflow: hidden;
    background: var(--pink);
    font-family: "Open Sans", sans-serif;
  }
  .backdrop { position: absolute; inset: 0; }

  .hero-scene {
    position: absolute;
    left: 0; top: 188px;
    width: 848px; height: 452px;
    background: linear-gradient(160deg, #f0b0b8 0%, #f4c2c6 45%, #e9a5b3 100%);
  }

  .logo-card {
    position: absolute;
    left: 30px; top: 20px;
    width: 256px; height: 310px;
    background: var(--white);
    display: flex;
    align-items: center;
    justify-content: center;
    gap: 10px;
  }
  .logo-card .mark {
    width: 18px; height: 18px;
    border-radius: 50%;
    background: var(--pink);
    flex: none;
  }
  .logo-card .brand {
    font-family: "Open Sans", sans-serif;
    font-weight: 700;
    font-size: 30px;
    line-height: 1.1;
    color: var(--pink);
    width: 150px;
  }

  .contact {
    position: absolute;
    left: 576px; top: 14px;
    margin: 0; padding: 0;
    list-style: none;
    font-family: "Roboto Condensed", sans-serif;
    font-weight: 700;
    color: var(--white);
    font-size: 16px;
    line-height: 1.12;
  }
  .contact li {
    display: flex;
    align-items: flex-start;
    gap: 22px;
    margin-bottom: 10px;
  }
  .contact svg { width: 16px; height: 16px; flex: none; margin-top: 2px; }
  .contact .note { font-size: 13px; }

  .headline {
    position: absolute;
    left: 410px; top: 208px;
    width: 386px; height: 218px;
    background: var(--purple);
    border-radius: 8px;
    text-align: center;
    color: var(--white);
    font-family: "Share Tech Mono", monospace;
    font-variant: small-caps;
  }
  .headline .line1 { position: absolute; left: 0; right: 0; top: 18px; font-size: 42px; letter-spacing: 2px; }
  .headline .line2 { position: absolute; left: 0; right: 0; top: 76px; font-size: 34px; }
  .headline .line3 { position: absolute; left: 0; right: 0; top: 122px; font-size: 44px; }
  .headline .note {
    position: absolute; left: 0; right: 0; top: 180px;
    font-family: "Open Sans", sans-serif;
    font-variant: normal;
    font-weight: 700;
    font-size: 19px;
    color: var(--ink);
  }

  .photo {
    position: absolute;
    background: var(--frame);
    padding: 8px;
    box-shadow: 0 3px 8px rgba(0,0,0,.25);
    box-sizing: border-box;
  }
  .photo .fill { width: 100%; height: 100%; }
  .photo-yoga { left: 66px; top: 500px; width: 262px; height: 240px; transform: rotate(-6deg); }
  .photo-yoga .fill { background: linear-gradient(150deg, #161616 0%, #2a2230 60%, #3c6e6a 100%); }
  .photo-soccer { left: 302px; top: 488px; width: 232px; height: 258px; transform: rotate(5deg); z-index: 2; }
  .photo-soccer .fill { background: linear-gradient(180deg, #c9d6c8 0%, #8aa06e 55%, #6b8a4b 100%); }
  .photo-study { left: 524px; top: 492px; width: 276px; height: 240px; transform: rotate(-6deg); z-index: 3; }
  .photo-study .fill { background: linear-gradient(130deg, #e8dcc6 0%, #c9a987 55%, #b5745c 100%); }

  .founder {
    position: absolute;
    left: 0; right: 0; top: 756px;
    text-align: center;
    font-family: "Cinzel", serif;
    font-weight: 600;
    color: var(--ink);
    font-size: 29px;
    line-height: 38px;
    letter-spacing: 1px;
  }

  .offer-title {
    position: absolute;
    left: 36px; top: 850px;
    margin: 0;
    font-family: "Share Tech Mono", monospace;
    font-variant: small-caps;
    font-weight: 400;
    font-size: 36px;
    color: var(--white);
    letter-spacing: 2px;
  }
  .offer-list {
    position: absolute;
    left: 0; right: 0; top: 896px;
    margin: 0; padding: 0;
    list-style: none;
    color: var(--white);
    font-weight: 700;
    font-size: 22.5px;
  }
  .offer-list .row { position: absolute; white-space: nowrap; display: flex; gap: 20px; }
  .offer-list .row1 { left: 14px; top: 0; }
  .offer-list .row2 { left: 42px; top: 42px; }
  .offer-list .row3 { left: 86px; top: 86px; gap: 22px; }
  .offer-list span { display: inline-flex; align-items: center; gap: 6px; }
  .offer-list svg { width: 14px; height: 14px; flex: none; }

  .hours {
    position: absolute;
    left: 0; right: 0;
    text-align: center;
    color: var(--ink);
    font-family: "Open Sans", sans-serif;
    font-weight: 700;
  }
  .hours-days { top: 1050px; font-size: 15px; text-transform: uppercase; letter-spacing: .2px; }
  .hours-time { top: 1092px; font-size: 16px; font-variant: small-caps; }

  .mission {
    position: absolute;
    right: 6px; top: 1128px;
    text-align: right;
    font-family: "Archivo", sans-serif;
    font-weight: 700;
    font-size: 16px;
    line-height: 21px;
    color: var(--white);
    text-shadow: 1px 1px 1px rgba(60,20,50,.7);
  }
</style>
</head>
<body>
<main class="flyer">
  <svg class="backdrop" width="848" height="1200" viewBox="0 0 848 1200" aria-hidden="true">
    <rect x="0" y="0" width="848" height="188" fill="var(--purple)"/>
    <polygon points="0,0 340,0 306,44 0,44" fill="var(--pink-soft)"/>
    <polygon points="574,176 848,176 848,188 566,188" fill="var(--pink-soft)"/>
    <rect x="0" y="640" width="848" height="560" fill="var(--pink)"/>
    <polygon points="530,1120 848,1120 848,1200 460,1200" fill="var(--purple)"/>
  </svg>

  <div class="hero-scene" role="img" aria-label="Softly tinted photo of a desk with a laptop, notebook, pencil and printed papers"></div>

  <div class="logo-card">
    <span class="mark" aria-hidden="true"></span>
    <span class="brand">Ridge Lass Crew</span>
  </div>

  <ul class="contact">
    <li>
      <svg viewBox="0 0 16 16" aria-hidden="true"><rect x="1" y="3" width="14" height="10" rx="1" fill="#fff"/><polyline points="1.5,3.5 8,9 14.5,3.5" fill="none" stroke="var(--purple)" stroke-width="1.4"/></svg>
      <span>info@ridgelasscrew.example.au</span>
    </li>
    <li>
      <svg viewBox="0 0 16 16" aria-hidden="true"><path d="M4 1.5 L6.5 4.5 L5 6.5 Q6.5 9.5 9.5 11 L11.5 9.5 L14.5 12 L12.5 14.5 Q6 14 1.5 3.5 Z" fill="#fff"/></svg>
      <span>0455817396</span>
    </li>
    <li>
      <svg viewBox="0 0 16 16" aria-hidden="true"><circle cx="8" cy="8" r="3" fill="#fff"/></svg>
      <span>http://fb.example/ridgelasscrew</span>
    </li>
    <li>
      <svg viewBox="0 0 16 16" aria-hidden="true"><path d="M8 1 A5 5 0 0 1 13 6 Q13 9.5 8 15 Q3 9.5 3 6 A5 5 0 0 1 8 1 Z" fill="#fff"/><circle cx="8" cy="6" r="2" fill="var(--purple)"/></svg>
      <span>87 Pelham Pde,<br>Baulkham Hills<br><span class="note">(across from Crestmoor Day Clinic)</span></span>
    </li>
  </ul>

  <section class="headline">
    <div class="line1">A Girls Only</div>
    <div class="line2">After School Program</div>
    <div class="line3">For 11-14yrs</div>
    <div class="note">as OSHC is no longer available</div>
  </section>

  <figure class="photo photo-yoga" style="margin:0"><div class="fill" role="img" aria-label="Photo of a girl in a purple top doing a yoga side plank"></div></figure>
  <figure class="photo photo-soccer" style="margin:0"><div class="fill" role="img" aria-label="Photo of a girl in an orange soccer kit heading a ball"></div></figure>
  <figure class="photo photo-study" style="margin:0"><div class="fill" role="img" aria-label="Photo of a young girl studying in a library"></div></figure>

  <h1 class="founder" style="margin:0">The Brainchild of Rebecca Folwin<br>Ridge Lass Crew</h1>

  <h2 class="offer-title">We look to offer</h2>
  <div class="offer-list">
    <div class="row row1">
      <span><svg viewBox="0 0 14 14"><circle cx="7" cy="7" r="6" fill="none" stroke="#fff" stroke-width="1.5"/><polyline points="4,7 6.2,9.2 10,5" fill="none" stroke="#fff" stroke-width="1.5"/></svg>Daily meditation</span>
      <span style="margin-left:10px"><svg viewBox="0 0 14 14"><circle cx="7" cy="7" r="6" fill="none" stroke="#fff" stroke-width="1.5"/><polyline points="4,7 6.2,9.2 10,5" fill="none" stroke="#fff" stroke-width="1.5"/></svg>Healthy snacks</span>
      <span><svg viewBox="0 0 14 14"><circle cx="7" cy="7" r="6" fill="none" stroke="#fff" stroke-width="1.5"/><polyline points="4,7 6.2,9.2 10,5" fill="none" stroke="#fff" stroke-width="1.5"/></svg>Dedicated homework time</span>
    </div>
    <div class="row row2">
      <span><svg viewBox="0 0 14 14"><circle cx="7" cy="7" r="6" fill="none" stroke="#fff" stroke-width="1.5"/><polyline points="4,7 6.2,9.2 10,5" fill="none" stroke="#fff" stroke-width="1.5"/></svg>Organised group activity,(yoga, fitness class, soccer etc.)</span>
    </div>
    <div class="row row3">
      <span><svg viewBox="0 0 14 14"><circle cx="7" cy="7" r="6" fill="none" stroke="#fff" stroke-width="1.5"/><polyline points="4,7 6.2,9.2 10,5" fill="none" stroke="#fff" stroke-width="1.5"/></svg>Regular guests speakers</span>
      <span><svg viewBox="0 0 14 14"><circle cx="7" cy="7" r="6" fill="none" stroke="#fff" stroke-width="1.5"/><polyline points="4,7 6.2,9.2 10,5" fill="none" stroke="#fff" stroke-width="1.5"/></svg>Social media free zone</span>
    </div>
  </div>

  <p class="hours hours-days" style="margin:0">Open every afternoon and during school holidays</p>
  <p class="hours hours-time" style="margin:0">3-6pm Monday to Friday</p>

  <p class="mission" style="margin:0">Dedicated to Coaching &amp; Mentoring<br>Our Girls into Strong, Independent<br>Young women</p>
</main>
</body>
</html>
```